Jolly Paws Business Card Update

I have a business card which I love. I want to keep the same logo, colours, font and style. I want to upgrade the scripting and remove some elements and add others.
On the front side under Services - remove the existing wording and insert - Providing individual coaching strategies to create happy, healthy and social canine companions
Under Denise Carvell amend the current wording to read: Qualified in Dog Behavioural Training, Natural Animal Healthcare and Animal Health Science
On the reverse side to remove the web address.

```html
<!DOCTYPE html>
<html lang="en">
<head>
<meta charset="utf-8">
<title>Jolly Paws Business Card</title>
<link rel="stylesheet" href="https://fonts.googleapis.com/css2?family=Arimo:wght@400&family=Open+Sans:ital,wght@0,400;0,600;0,700;1,400&display=swap">
<style>
  :root {
    --backdrop: #2a2a2b;
    --blue-deep: #263a8a;
    --blue-mid: #1b5aa8;
    --blue-light: #0a86cb;
    --red: #c41c24;
    --red-dark: #8e1a1e;
    --cream: #efe6cf;
    --white: #ffffff;
    --navy: #1d2d5c;
  }
  * { margin: 0; padding: 0; box-sizing: border-box; }
  html, body { width: 1138px; height: 1200px; overflow: hidden; }
  body { background: var(--backdrop); position: relative; font-family: "Open Sans", sans-serif; color: var(--white); }

  .card {
    position: absolute; top: 276px; width: 375px; height: 620px;
    border-radius: 14px; overflow: hidden;
    background: linear-gradient(200deg, var(--blue-deep) 0%, var(--blue-mid) 45%, var(--blue-light) 100%);
    text-align: center;
  }
  .card--front { left: 156px; }
  .card--back { left: 577px; }

  .brand-mark {
    position: absolute; left: 50%; top: 59px; width: 150px; height: 150px; margin-left: -75px;
    border-radius: 50%; background: var(--cream); border: 7px solid var(--red);
  }
  .brand-name {
    position: absolute; left: 0; right: 0; top: 224px;
    font-family: "Open Sans", sans-serif; font-weight: 600; font-size: 34px; letter-spacing: 1px;
    color: var(--white); line-height: 1;
  }
  .tagline {
    position: absolute; left: 0; right: 0; top: 266px;
    font-family: "Arimo", sans-serif; font-size: 17px; letter-spacing: 0.3px; color: #e8ecf5;
  }

  .person-name {
    position: absolute; left: 0; right: 0; top: 340px;
    font-weight: 600; font-size: 25px; color: #f3f4f8;
  }
  .credentials {
    position: absolute; left: 0; right: 0; top: 372px;
    font-style: italic; font-size: 15.5px; line-height: 21px; color: #e6eaf4;
  }

  .contact-divider {
    position: absolute; left: 78px; right: 78px; top: 468px; height: 24px;
    display: flex; align-items: center; justify-content: center; gap: 4px;
  }
  .contact-divider .rule { flex: 1; height: 2px; background: var(--red); }
  .contact-divider .rule--left { margin-right: 10px; background: linear-gradient(90deg, transparent, var(--red)); }
  .contact-divider .rule--right { margin-left: 10px; background: linear-gradient(90deg, var(--red), transparent); }
  .contact-divider svg { width: 22px; height: 22px; }

  .contact-list {
    position: absolute; left: 0; right: 0; top: 505px;
    list-style: none; font-size: 16px; line-height: 23px; color: #f0f3f9;
  }

  .services-band {
    position: absolute; left: 0; right: 0; top: 371px; height: 127px;
    background: radial-gradient(ellipse at 50% 60%, #e0242a 0%, var(--red) 45%, var(--red-dark) 100%);
  }
  .services-label {
    position: absolute; left: 50%; top: 354px; width: 186px; margin-left: -93px; height: 30px;
    border-radius: 15px; background: var(--white); border: 3px solid var(--blue-mid);
    font-weight: 700; font-size: 19px; letter-spacing: 2px; line-height: 24px; color: var(--navy);
  }
  .services-text {
    position: absolute; left: 40px; right: 40px; top: 403px;
    font-family: "Arimo", sans-serif; font-size: 15.5px; line-height: 20px; text-transform: uppercase; color: var(--white);
  }
  .mission {
    position: absolute; left: 60px; right: 60px; top: 526px;
    font-family: "Arimo", sans-serif; font-size: 16.5px; line-height: 19.5px; color: var(--white);
  }
</style>
</head>
<body>

<section class="card card--front">
  <div class="brand-mark" aria-hidden="true"></div>
  <div class="brand-name">JOLLY PAWS</div>
  <div class="tagline">HAPPY DOGS, HAPPY OWNERS</div>
  <div class="person-name">Denise Carvell</div>
  <p class="credentials">Qualified in Dog Behavioural Training,<br>Natural Animal Healthcare and<br>Animal Health Science</p>
  <div class="contact-divider">
    <span class="rule rule--left"></span>
    <svg viewBox="0 0 22 22" aria-label="Phone"><circle cx="11" cy="11" r="9.5" fill="#2a4f9e" stroke="#c41c24" stroke-width="2"/><path d="M7 9c0-1 1-2 4-2s4 1 4 2l-1.5 1-1-1h-3l-1 1zM8 11h6l1 4H7z" fill="#fff"/></svg>
    <svg viewBox="0 0 22 22" aria-label="Email"><circle cx="11" cy="11" r="9.5" fill="#2a4f9e" stroke="#c41c24" stroke-width="2"/><rect x="6" y="7.5" width="10" height="7" fill="#fff"/><path d="M6 7.5l5 4 5-4" fill="none" stroke="#2a4f9e" stroke-width="1"/></svg>
    <svg viewBox="0 0 22 22" aria-label="Website"><circle cx="11" cy="11" r="9.5" fill="#2a4f9e" stroke="#c41c24" stroke-width="2"/><g fill="none" stroke="#fff" stroke-width="1"><circle cx="11" cy="11" r="5"/><ellipse cx="11" cy="11" rx="2.2" ry="5"/><path d="M6 11h10"/></g></svg>
    <span class="rule rule--right"></span>
  </div>
  <ul class="contact-list">
    <li>0412 587630</li>
    <li>hello@jollypawsco.com</li>
    <li>www.jollypawsco.com</li>
  </ul>
</section>

<section class="card card--back">
  <div class="brand-mark" aria-hidden="true"></div>
  <div class="brand-name">JOLLY PAWS</div>
  <div class="tagline">HAPPY DOGS, HAPPY OWNERS</div>
  <div class="services-band"></div>
  <div class="services-label">SERVICES</div>
  <p class="services-text">Providing individual coaching strategies to create happy, healthy and social canine companions</p>
  <p class="mission">Promoting communication and connection between dogs and their families</p>
</section>

</body>
</html>
```